Website redesign for a Medical Office

We are a physician office in need of a website redesign and a face-lift.
1.Website must work on all platforms including mobile phones and tablets.
2.Website will also include and interactive CONTACT US form and payment gateway for office to collect payment from patients online.
3.Website should have the ability for us to easily edit content without resorting to the services of an IT person.
4. Website content will be collected from the present website www.sunbrookkids.com.
- The type of upgrade we are looking for is more of a corrective work. The major problems with the current website are:
1. Contact Us form not working correctly
2. Credit card/monetrix gateway not working as intended
3. Needing better images/pictures to correctly reflect our business.
4. General enhancement to the overall feel and outlook of the current website.

5. Once a design is selected, website MUST be up and live within TWO WEEKS. The designer able to make this work within the time-frame will get an extra bonus.

Target Market(s)

General public; including patients and their parents.

Industry/Entity Type

Healthcare

Coding

Coded - Design and coding required

Number of Pages Required

5+ page

Font styles to use
Sans Serif

Colors
0492cd
33a6d7
85cae6
cee9f5
cedeed
acd036
cadf82
00a990
f04a50

Requirements
Must have
• 1. Ability for the website to work on all platforms including mobile phones and tablets.
• 2. Include an interactive CONTACT US form
• 3. A payment gateway for office to collect payment from patients online using credit cards and Monetrix.
• 4. Website should have the ability for us to easily edit content without resorting to the services of an IT person.
• 5. Once a design is selected, website MUST be up and live within TWO WEEKS.
• 6. Social network buttons.
• 7. A Vorlund map with office location or geo-tag and directions to office.
Nice to have
• Nice theme, children friendly with a flashy home page and inside pages.
• Attractive design with wow factor

```html
<!DOCTYPE html>
<html lang="en">
<head>
<meta charset="utf-8">
<title>Sunbrook Pediatrics</title>
<link href="https://fonts.googleapis.com/css2?family=Open+Sans:ital,wght@0,400;0,600;0,700;1,400&display=swap" rel="stylesheet">
<style>
:root{
  --blue:#0492cd;--blue-mid:#33a6d7;--blue-soft:#85cae6;--blue-pale:#cee9f5;--grey-blue:#cedeed;
  --green:#acd036;--green-soft:#cadf82;--teal:#00a990;--red:#f04a50;--red-light:#f4676c;
  --ink:#3a3a3a;--muted:#8a8a8a;--white:#fff;
}
*{margin:0;padding:0;box-sizing:border-box}
html,body{width:1200px;height:3226px;overflow:hidden;background:#fff}
body{font-family:"Open Sans",sans-serif;color:var(--ink);position:relative}
.abs{position:absolute}
/* header */
.site-header{position:absolute;left:0;top:0;width:1200px;height:97px;background:#fff;z-index:3}
.brand{position:absolute;left:133px;top:24px;display:flex;align-items:center;gap:10px}
.brand-mark{width:40px;height:40px;background:var(--blue);border-radius:4px}
.brand-name{font-weight:700;font-size:20px;color:var(--blue);line-height:1;letter-spacing:.5px}
.nav a{position:absolute;top:38px;font-size:15px;color:#666;text-decoration:none}
.nav a.active{color:var(--red)}
.nav a.active::before{content:"";position:absolute;left:-4px;right:-4px;top:-38px;height:3px;background:var(--red)}
/* hero */
.hero{position:absolute;left:0;top:97px;width:1200px;height:537px;background:linear-gradient(180deg,#4d9be6 0%,#8cc3f0 45%,#d8ebf8 100%)}
.hero-photo{position:absolute;left:290px;top:210px;width:620px;height:327px;background:linear-gradient(180deg,#e9c9a8,#d98a70 60%,#c85a5a);border-radius:6px 6px 0 0;opacity:.85}
.hero h1{position:absolute;left:0;width:1200px;top:70px;text-align:center;color:#fff;font-weight:600;font-size:34px;line-height:42px}
.btn{display:inline-block;border-radius:24px;color:#fff;font-size:12px;font-weight:700;text-align:center;text-transform:uppercase}
.hero .btn{position:absolute;left:519px;top:158px;width:137px;height:42px;line-height:42px;background:var(--red)}
.hero .arrow{position:absolute;top:247px}
/* services */
.section-title{position:absolute;left:0;width:1200px;text-align:center;font-size:28px;font-weight:400}
.services-title{top:670px;color:var(--blue-mid)}
.baby-photo{position:absolute;left:462px;top:731px;width:250px;height:346px;background:radial-gradient(ellipse at 50% 45%,#f4dccb,#efe7e2 65%,#fff 100%)}
.service{position:absolute;width:300px}
.service h3{font-size:16px;font-weight:400;color:#444;margin-bottom:6px}
.service p{font-size:10.5px;line-height:15px;color:var(--muted)}
.service.left{text-align:right}
.icon-box{position:absolute;width:66px;height:66px;border-radius:10px}
/* about */
.about{position:absolute;left:0;top:1097px;width:1200px;height:451px;background:linear-gradient(90deg,#eef3fa 0%,#e6eef8 40%,#d9e4ef 100%)}
.about-photo{position:absolute;left:495px;top:0;width:705px;height:451px;background:linear-gradient(90deg,rgba(230,238,248,0) 0%,#d6dfe8 30%,#c9d3dc 100%)}
.about h2{position:absolute;left:161px;font-weight:400;font-size:32px;line-height:40px}
.about .kicker{top:70px;color:var(--green)}
.about .name{top:110px;color:#3a3a3a}
.about p{position:absolute;left:161px;top:168px;width:470px;font-size:13px;line-height:26px;color:#777}
.about .btn{position:absolute;left:157px;top:308px;width:135px;height:40px;line-height:40px;background:var(--blue-mid)}
/* archives */
.archives-title{top:1592px;color:#333;font-size:27px}
.card{position:absolute;top:1651px;width:303px;height:366px;background:#fff;border:1px solid #e2e2e2}
.card .thumb{height:194px}
.card h4{margin:26px 0 0 24px;font-size:14.5px;font-weight:400;color:var(--blue-mid)}
.card .date{margin:4px 0 0 24px;font-size:12px;color:#555}
.card p{margin:8px 24px 0 24px;font-size:11.5px;line-height:20px;color:#999}
.card .more{display:block;margin:8px 0 0 24px;font-size:11.5px;color:var(--red)}
/* testimonials */
.testimonials{position:absolute;left:0;top:2053px;width:1200px;height:404px}
.testimonials h2{position:absolute;left:0;width:1200px;top:112px;text-align:center;color:#fff;font-weight:400;font-size:30px}
.avatar{position:absolute;left:211px;top:144px;width:193px;height:193px;border-radius:50%;border:6px solid #fff;background:radial-gradient(circle at 50% 40%,#f3d7c4,#d7a88e)}
.quote{position:absolute;left:445px;top:186px;width:600px;color:#fff;font-style:italic;font-size:15px;line-height:31px;white-space:nowrap}
.quote-author{position:absolute;left:445px;top:280px;color:#fff;font-size:15px}
.qmark{position:absolute;color:#fff;font-size:56px;font-weight:700;line-height:1}
/* map */
.map{position:absolute;left:0;top:2457px;width:1200px;height:403px;background:linear-gradient(135deg,#ececec,#e2e2e2 60%,#dcdcdc)}
/* footer */
.footer{position:absolute;left:0;top:2860px;width:1200px;height:300px;background:var(--red);color:#fff}
.footer h5{position:absolute;top:52px;font-size:18px;font-weight:400}
.footer ul{position:absolute;top:90px;list-style:none;font-size:12.5px;line-height:30px}
.contact-lines{position:absolute;left:516px;top:90px;font-size:13px;line-height:22px}
.contact-lines .phone{font-size:15px;margin-top:10px}
.subscribe{position:absolute;left:770px;top:98px;width:294px;height:37px;background:#fff;border-radius:20px}
.subscribe span{position:absolute;left:20px;top:10px;font-size:12px;color:#aaa}
.subscribe b{position:absolute;right:5px;top:5px;width:88px;height:27px;line-height:27px;text-align:center;background:var(--green);border-radius:14px;font-size:12px;font-weight:600;color:#fff}
.social{position:absolute;top:153px;width:30px;height:30px;border:2px solid #fff;border-radius:50%}
.pay{position:absolute;top:210px;width:44px;height:24px;background:#fff;border-radius:3px;color:#555;font-size:9px;font-weight:600;text-align:center;line-height:24px}
.footer-bar{position:absolute;left:0;top:3160px;width:1200px;height:66px;background:var(--red-light);color:#fff;font-size:12px;text-align:center;line-height:66px}
</style>
</head>
<body>

<header class="site-header">
  <div class="brand"><span class="brand-mark"></span><span class="brand-name">SUNBROOK<br>PEDIATRICS</span></div>
  <nav class="nav">
    <a class="active" style="left:430px">Home</a>
    <a style="left:503px">About Us</a>
    <a style="left:600px">Services</a>
    <a style="left:690px">Sun Health Center</a>
    <a style="left:866px">Forms</a>
    <a style="left:940px">News</a>
    <a style="left:1010px">Contact</a>
  </nav>
</header>

<section class="hero">
  <div class="hero-photo" role="img" aria-label="Group of five happy children raising their arms against a cloudy sky"></div>
  <h1>Modern Pediatric to the Health and<br>Wellness of Childrens</h1>
  <a class="btn">Learn More</a>
  <svg class="arrow" style="left:122px" width="24" height="40" viewBox="0 0 24 40"><path d="M20 4 4 20l16 16" fill="none" stroke="#fff" stroke-width="4"/></svg>
  <svg class="arrow" style="left:1056px" width="24" height="40" viewBox="0 0 24 40"><path d="M4 4l16 16L4 36" fill="none" stroke="#fff" stroke-width="4"/></svg>
</section>

<section class="services">
  <h2 class="section-title services-title">What We Do</h2>
  <div class="baby-photo" role="img" aria-label="Smiling baby crawling"></div>

  <div class="service left" style="left:80px;top:772px">
    <h3>General Medical Care</h3>
    <p>Routine Office visits for common ailments,<br>Immunizations, ADHD Evaluation</p>
  </div>
  <div class="icon-box" style="left:400px;top:768px;background:var(--green)">
    <svg width="66" height="66" viewBox="0 0 66 66"><path d="M22 18v12a9 9 0 0 0 18 0V18M31 39v6a8 8 0 0 0 16 0v-5" fill="none" stroke="#fff" stroke-width="3"/><circle cx="47" cy="36" r="4" fill="none" stroke="#fff" stroke-width="3"/></svg>
  </div>

  <div class="service left" style="left:80px;top:912px">
    <h3>Newborn Care</h3>
    <p>Routine Annual Physicals, Sports Physicals,<br>School and College Physicals.</p>
  </div>
  <div class="icon-box" style="left:400px;top:910px;background:var(--red)">
    <svg width="66" height="66" viewBox="0 0 66 66"><ellipse cx="33" cy="34" rx="11" ry="15" fill="none" stroke="#fff" stroke-width="3"/><circle cx="33" cy="28" r="5" fill="none" stroke="#fff" stroke-width="3"/></svg>
  </div>

  <div class="icon-box" style="left:733px;top:768px;background:var(--blue-mid)">
    <svg width="66" height="66" viewBox="0 0 66 66"><path d="M20 46l6-6M24 36l14-14 6 6-14 14zM40 20l6 6M44 16l6 6" fill="none" stroke="#fff" stroke-width="3"/></svg>
  </div>
  <div class="service" style="left:821px;top:772px">
    <h3>Physical Examinations</h3>
    <p>Evaluation of the newborn, Infant<br>circumcision</p>
  </div>

  <div class="icon-box" style="left:733px;top:910px;background:var(--teal)">
    <svg width="66" height="66" viewBox="0 0 66 66"><path d="M33 48S16 37 16 26a8 8 0 0 1 17-3 8 8 0 0 1 17 3c0 11-17 22-17 22z" fill="none" stroke="#fff" stroke-width="3"/><path d="M33 28v10M28 33h10" stroke="#fff" stroke-width="3"/></svg>
  </div>
  <div class="service" style="left:821px;top:912px">
    <h3>Emergency Care</h3>
    <p>Management of simple injuries, Strains<br>and sprains, Lacerations, Drainage</p>
  </div>
</section>

<section class="about">
  <div class="about-photo" role="img" aria-label="Mother lying on a bed lifting her laughing baby"></div>
  <h2 class="kicker">Little About</h2>
  <h2 class="name">Sunbrook Pediatrics</h2>
  <p>Sunbrook Pediatrics is a modern pediatric practice dedicated to the health and wellness of children. It is the pediatrician office of choice in Harlow, Georgia. At Sunbrook Pediatrics, you will find a pediatrician and an environment that is warm and compassionate. All of our staff members are knowledgeable, caring, efficient, and ready to serve you.</p>
  <a class="btn">Learn More</a>
</section>

<section class="archives">
  <h2 class="section-title archives-title">From Our Medical Archives</h2>
  <article class="card" style="left:131px">
    <div class="thumb" role="img" aria-label="Sick child in bed with a medicine bottle" style="background:linear-gradient(135deg,#f1d2bd,#d9b7a0 60%,#c86a45)"></div>
    <h4>Common Childhood Illnesses</h4>
    <div class="date">14 December, 2016, by Admin</div>
    <p>As they grow and develop, children come in contact with and may sometimes suffer from a variety of common illnesses....</p>
    <a class="more">READ MORE</a>
  </article>
  <article class="card" style="left:447px">
    <div class="thumb" role="img" aria-label="Pregnant woman resting on a sofa" style="background:linear-gradient(135deg,#f4f4f4,#e9dcd3 50%,#6d9bd6)"></div>
    <h4>Now That You Are Pregnant</h4>
    <div class="date">14 December, 2016, by Admin</div>
    <p>As they grow and develop, children come in contact with and may sometimes suffer from a variety of common illnesses....</p>
    <a class="more">READ MORE</a>
  </article>
  <article class="card" style="left:768px">
    <div class="thumb" role="img" aria-label="Mother sleeping beside her newborn" style="background:linear-gradient(135deg,#e6e9ef,#e2c6b4 50%,#f2f2f4)"></div>
    <h4>Newborn Care</h4>
    <div class="date">14 December, 2016, by Admin</div>
    <p>As they grow and develop, children come in contact with and may sometimes suffer from a variety of common illnesses....</p>
    <a class="more">READ MORE</a>
  </article>
</section>

<section class="testimonials">
  <svg class="abs" style="left:0;top:0" width="1200" height="404" viewBox="0 0 1200 404" preserveAspectRatio="none">
    <path d="M0 0Q600 90 1200 0V404H0Z" fill="var(--green)"/>
    <path d="M0 28Q600 112 1200 28" fill="none" stroke="#fff" stroke-width="2" stroke-dasharray="6 6"/>
  </svg>
  <h2>Testimonials</h2>
  <div class="avatar" role="img" aria-label="Portrait of a mother hugging her child"></div>
  <span class="qmark" style="left:405px;top:176px">&ldquo;</span>
  <p class="quote">Proesent elementum elit at tellus nec ultricies sit amet porttitor mattis<br>enim In massa libero interdum nec interdum vel blandit sed nulla In<br>ullamcorper est eget tempor cursus neque mi consectetu</p>
  <span class="qmark" style="left:866px;top:252px">&rdquo;</span>
  <div class="quote-author">-Elena Marie Ross</div>
  <svg class="abs" style="left:136px;top:200px" width="22" height="36" viewBox="0 0 22 36"><path d="M18 3 4 18l14 15" fill="none" stroke="#fff" stroke-width="4"/></svg>
  <svg class="abs" style="left:1022px;top:200px" width="22" height="36" viewBox="0 0 22 36"><path d="M4 3l14 15L4 33" fill="none" stroke="#fff" stroke-width="4"/></svg>
</section>

<div class="map" role="img" aria-label="Street map showing the office location in Harlow, Georgia"></div>

<footer class="footer">
  <h5 style="left:133px">Information</h5>
  <ul style="left:133px"><li>About Us</li><li>Why Our Product</li><li>Blogs</li><li>Testimonials</li></ul>
  <h5 style="left:327px">Rsources</h5>
  <ul style="left:327px"><li>Support</li><li>Shop Now</li><li>Best Sellings</li><li>Why buy from us</li></ul>
  <h5 style="left:516px">Contact Information</h5>
  <div class="contact-lines">
    <div>Sunbrook Pediatrics 22B Willow Crest<br>Harlow, GA 30199</div>
    <div class="phone">(555)-014-2290</div>
    <div style="margin-top:6px">www.sunbrookkids.com</div>
  </div>
  <h5 style="left:770px">Stay Update</h5>
  <div class="subscribe"><span>Email address</span><b>Subscribe</b></div>
  <span class="social" style="left:772px"></span>
  <span class="social" style="left:808px"></span>
  <span class="social" style="left:844px"></span>
  <span class="social" style="left:880px"></span>
  <span class="pay" style="left:772px">Cardela</span>
  <span class="pay" style="left:824px">Tallon</span>
  <span class="pay" style="left:876px">Brisca</span>
  <span class="pay" style="left:928px">Quorra</span>
  <span class="pay" style="left:980px">Monetrix</span>
</footer>
<div class="footer-bar">&copy; 2017 Company Name &nbsp;All right reserved &nbsp;Term of Use</div>

</body>
</html>
```